Heron Haulage needs Bussiness cards!

Our new trucking company needs business cards!
We need the same design with two different names and emails, everything else it's the same.
I have included our original logo so we can use it for the design.
Note: the logo to be used is the o e with the buffalo on the right side, next to the letters H and H.

Target Market(s)

Trucking, refrigerated transportation, freight

Industry/Entity Type

Business

Contact Information for Business Card

Card #1:
Marcus Whitfield
marcuswhitfield@heronhaulage.example
1-855-317-6094
(956)238-7160
4117 W. Larkin Ave.
Pharr, TX 78590
www.heronhaulage.example

Card#2:
Rosalba Quintero
rosalba@heronhaulage.example
1-855-317-6094
(956)238-7160
4117 W. Larkin Ave.
Pharr, TX 78590
www.heronhaulage.example

Font styles to use
Sans Serif

Colors
0655a3
ec1f27
ffffff

Requirements
Must have
• our logo
Nice to have
• roads on background,

```html
<!DOCTYPE html>
<html lang="en">
<head>
<meta charset="utf-8">
<title>Heron Haulage – Business Card</title>
<link href="https://fonts.googleapis.com/css2?family=Montserrat:wght@400;500;700;800&display=swap" rel="stylesheet">
<style>
  :root {
    --navy: #0c2c57;
    --navy-text: #123a6d;
    --red: #c8102e;
    --white: #ffffff;
    --backdrop: #2b2b2d;
  }
  * { box-sizing: border-box; margin: 0; padding: 0; }
  html, body {
    width: 1200px; height: 900px; overflow: hidden;
    background: var(--backdrop);
    font-family: "Montserrat", sans-serif;
  }
  .stage { position: relative; width: 1200px; height: 900px; }
  .card {
    position: absolute; width: 620px; height: 354px;
    border-radius: 22px; overflow: hidden;
  }
  .card-front { left: 120px; top: 70px; background: var(--navy); }
  .card-back { left: 460px; top: 476px; background: var(--white); }

  .wordmark {
    position: absolute; display: flex; align-items: center; gap: 12px;
    font-weight: 800; letter-spacing: -0.5px; line-height: 1;
  }
  .wordmark-dot { border-radius: 50%; flex: none; }
  .card-front .wordmark { left: 150px; top: 130px; font-size: 44px; color: var(--white); }
  .card-front .wordmark-dot { width: 30px; height: 30px; background: var(--red); }
  .front-url {
    position: absolute; left: 0; right: 0; top: 290px; text-align: center;
    color: var(--white); font-size: 17px; font-weight: 500; letter-spacing: 0.3px;
  }

  .card-back .wordmark { left: 36px; top: 200px; font-size: 25px; color: var(--navy-text); gap: 8px; }
  .card-back .wordmark-dot { width: 18px; height: 18px; background: var(--red); }
  .divider {
    position: absolute; left: 268px; top: 80px; width: 2px; height: 190px;
    background: linear-gradient(to bottom, var(--red), rgba(200,16,46,0.1));
  }
  .details { position: absolute; left: 284px; top: 86px; color: var(--navy-text); }
  .person-name { color: var(--red); font-size: 22px; font-weight: 700; letter-spacing: 0.5px; margin-bottom: 8px; }
  .address { font-size: 14px; line-height: 1.35; margin-bottom: 6px; }
  .contact-list { list-style: none; font-size: 13px; line-height: 1.5; }
  .contact-list li { display: flex; align-items: center; gap: 7px; }
  .contact-list svg { width: 12px; height: 12px; flex: none; }
</style>
</head>
<body>
<main class="stage">
  <section class="card card-front" aria-label="Card front">
    <div class="wordmark"><span class="wordmark-dot"></span><span>Heron Haulage</span></div>
    <p class="front-url">www.heronhaulage.example</p>
  </section>

  <section class="card card-back" aria-label="Card back">
    <div class="wordmark"><span class="wordmark-dot"></span><span>Heron Haulage</span></div>
    <div class="divider"></div>
    <div class="details">
      <h1 class="person-name">MARCUS WHITFIELD</h1>
      <p class="address">4117 W. Larkin Ave.<br>Pharr, TX 78590</p>
      <ul class="contact-list">
        <li>
          <svg viewBox="0 0 12 12"><path d="M2.5 1 L4.5 1 L5.2 3.5 L4 4.5 Q5 7 7.5 8 L8.5 6.8 L11 7.5 L11 9.5 Q10.5 11 9 11 Q1 10 1 3 Q1 1.5 2.5 1 Z" fill="#c8102e"/></svg>
          <span>1-855-317-6094</span>
        </li>
        <li>
          <svg viewBox="0 0 12 12"><rect x="3" y="0.8" width="6" height="10.4" rx="1.2" fill="none" stroke="#c8102e" stroke-width="1.2"/><circle cx="6" cy="9.2" r="0.7" fill="#c8102e"/></svg>
          <span>(956)238-7160</span>
        </li>
        <li>
          <svg viewBox="0 0 12 12"><rect x="0.8" y="2.5" width="10.4" height="7" rx="0.8" fill="none" stroke="#c8102e" stroke-width="1.2"/><path d="M1 3 L6 6.8 L11 3" fill="none" stroke="#c8102e" stroke-width="1.2"/></svg>
          <span>www.heronhaulage.example</span>
        </li>
        <li>
          <svg viewBox="0 0 12 12"><circle cx="6" cy="6" r="5" fill="none" stroke="#c8102e" stroke-width="1.1"/><ellipse cx="6" cy="6" rx="2.2" ry="5" fill="none" stroke="#c8102e" stroke-width="1"/><path d="M1 6 H11" stroke="#c8102e" stroke-width="1"/></svg>
          <span>marcuswhitfield@heronhaulage.example</span>
        </li>
      </ul>
    </div>
  </section>
</main>
</body>
</html>
```